Seeking funky, innovative business cards

I am looking to refresh our current business cards to something more engaging, visual and impactful. We are a management consultancy firm, see website (www.larkstone-partners.com.au). I've included our colour scheme, sample of the slides we use and our old business cards. We would like our cards to have icons. The card should display:- Name- Title- Mobile number- Address- Email address- Website - Company logo- Our purpose statement "We create the best places on earth to work"

Contact Information for Business Card

Brennan Ulfsson
Consultant
0468 927 341
Level 3, 218 Wexley Street, Melbourne 3000
brennan@larkstone-partners.com.au
www.larkstone-partners.com.au

Purpose statement "we create the best places on earth to work"
LOGO available in google images

Font styles to use
Other font styles liked:
• Open Sans Light, Bebas Neue (open to other cool foints)

Colors
ffc214
5c5c5c
f5f5f5
fefefe

Requirements
Must have
• - Name
• - Title
• - Mobile number
• - Address
• - Email address
• - Website
• - Company logo
• - Our purpose statement "We create the best places on earth to work"
Nice to have
• - Icons
• - Colour (see our colour scheme"

```html
<!DOCTYPE html>
<html lang="en">
<head>
<meta charset="utf-8">
<title>Larkstone Partners – Business Card</title>
<link rel="stylesheet" href="https://fonts.googleapis.com/css2?family=Lato:wght@300;400;700&display=swap">
<style>
  :root {
    --stage: #9a9a9a;
    --charcoal: #414344;
    --grey: #5c5c5c;
    --paper: #fefefe;
    --yellow: #ffc214;
    --amber: #f7a42f;
    --text: #3a3a3a;
  }
  * { box-sizing: border-box; margin: 0; padding: 0; }
  html, body { width: 1200px; height: 930px; overflow: hidden; }
  body {
    background: var(--stage);
    font-family: "Lato", sans-serif;
    position: relative;
  }
  .card {
    position: absolute;
    width: 560px;
    height: 320px;
    border-radius: 22px;
    overflow: hidden;
  }
  /* Back of card */
  .card-back {
    left: 90px; top: 80px;
    background: var(--charcoal);
  }
  .card-back .brand {
    position: absolute;
    left: 0; right: 0; top: 120px;
    text-align: center;
    color: var(--paper);
    font-weight: 300;
    font-size: 56px;
    letter-spacing: -1px;
  }
  .card-back .purpose {
    position: absolute;
    left: 0; right: 0; top: 255px;
    text-align: center;
    color: var(--yellow);
    font-size: 17px;
    font-weight: 400;
  }
  /* Front of card */
  .card-front {
    left: 560px; top: 530px;
    background: var(--paper);
  }
  .swoosh {
    position: absolute;
    left: 0; top: 0;
    width: 560px; height: 320px;
  }
  .card-front .brand {
    position: absolute;
    left: 34px; top: 52px;
    color: var(--grey);
    font-weight: 300;
    font-size: 28px;
    letter-spacing: -0.5px;
    display: flex;
    align-items: center;
    gap: 9px;
  }
  .brand-dot {
    width: 11px; height: 11px;
    border-radius: 50%;
    background: var(--yellow);
  }
  .person {
    position: absolute;
    right: 34px; top: 38px;
    text-align: right;
  }
  .person-name {
    color: var(--yellow);
    font-size: 24px;
    font-weight: 400;
    letter-spacing: 0.5px;
    text-transform: uppercase;
  }
  .person-title {
    color: var(--text);
    font-size: 15px;
    margin-top: 2px;
  }
  .divider {
    position: absolute;
    left: 34px; right: 34px; top: 150px;
    height: 1px;
    background: var(--yellow);
  }
  .address {
    position: absolute;
    right: 34px; top: 164px;
    text-align: right;
    color: var(--text);
    font-size: 15px;
    line-height: 1.35;
  }
  .contacts {
    position: absolute;
    left: 34px; top: 168px;
    list-style: none;
    color: var(--text);
    font-size: 15px;
    line-height: 1.4;
  }
  .contacts li { display: flex; align-items: center; gap: 10px; }
  .contacts svg { width: 12px; height: 12px; flex: none; }
</style>
</head>
<body>

<section class="card card-back" aria-label="Card back">
  <div class="brand">Larkstone Partners</div>
  <p class="purpose">We create the best places on earth to work</p>
</section>

<section class="card card-front" aria-label="Card front">
  <svg class="swoosh" viewBox="0 0 560 320" aria-hidden="true">
    <defs>
      <linearGradient id="waveFill" x1="0" y1="0" x2="1" y2="0">
        <stop offset="0" stop-color="#ffd21a"/>
        <stop offset="1" stop-color="#f7a42f"/>
      </linearGradient>
    </defs>
    <path d="M0 300 C150 305 300 290 400 252 C460 230 510 222 560 220 L560 320 L0 320 Z" fill="var(--charcoal)"/>
    <path d="M0 309 C160 313 310 300 410 262 C470 238 515 230 560 228 L560 320 L0 320 Z" fill="url(#waveFill)"/>
  </svg>

  <div class="brand"><span class="brand-dot"></span>Larkstone Partners</div>

  <div class="person">
    <div class="person-name">Brennan Ulfsson</div>
    <div class="person-title">Consultant</div>
  </div>

  <div class="divider"></div>

  <p class="address">Level 3, 218 Wexley Street<br>Melbourne 3000</p>

  <ul class="contacts">
    <li>
      <svg viewBox="0 0 12 12" aria-hidden="true"><path d="M2 1 L4 1 L5 3.5 L3.8 4.5 C4.5 6 6 7.5 7.5 8.2 L8.5 7 L11 8 L11 10 C11 10.6 10.5 11 10 11 C5 11 1 7 1 2 C1 1.5 1.4 1 2 1 Z" fill="var(--yellow)"/></svg>
      0468 927 341
    </li>
    <li>
      <svg viewBox="0 0 12 12" aria-hidden="true"><rect x="2.5" y="1" width="7" height="3" fill="var(--yellow)"/><rect x="1" y="4" width="10" height="5" rx="1" fill="var(--yellow)"/><rect x="3" y="7.5" width="6" height="3.5" fill="var(--yellow)"/></svg>
      +61 3 9573 4419
    </li>
    <li>
      <svg viewBox="0 0 12 12" aria-hidden="true"><rect x="1" y="2.5" width="10" height="7" fill="none" stroke="var(--yellow)" stroke-width="1.2"/><path d="M1 2.5 L6 6.5 L11 2.5" fill="none" stroke="var(--yellow)" stroke-width="1.2"/></svg>
      brennan@larkstone-partners.com.au
    </li>
    <li>
      <svg viewBox="0 0 12 12" aria-hidden="true"><circle cx="6" cy="6" r="5" fill="none" stroke="var(--yellow)" stroke-width="1.2"/><path d="M1 6 H11 M6 1 C3.5 3.5 3.5 8.5 6 11 M6 1 C8.5 3.5 8.5 8.5 6 11" fill="none" stroke="var(--yellow)" stroke-width="1"/></svg>
      www.larkstone-partners.com.au
    </li>
  </ul>
</section>

</body>
</html>
```